PowerPoint Design for KESTREL Polls

KESTREL Polls stands for 'Kindred Evaluation Scales Tracking Regional Electoral Leanings'. It is a collaborative research effort to format and combine multiple sources of public opinion data from around the world into merged datasets. We need a Microsoft PowerPoint design for our conference/workshop presentations and instructional videos used as part of our research efforts and crowdsourced development. The design should match the website design and logo, which are attached to this contest (these are the files from previous successful design contests).

Slides will contain a lot of data visualizations, tables with statistical output (lots of numbers), and figures. Bullet points will be used frequently on slides and larg blocks of text should be avided. Margins should be narrow to maximize space used and the size of fonts must be large enough (24-32+) to be visible at the back of classrooms and conference rooms.
Updates

I was away at a conference and am now busy with teaching preparation, so I need a few extra days to give adequate feedback.

Target Market(s)

academia, government, non-profits, postgraduates, researchers

Font styles to use
Sans Serif

Colors

Designer to choose colors to be used in the design.

Requirements
Must have
• designs for common slide layouts
Nice to have
• thematic link with website design and logo

```html
<!DOCTYPE html>
<html lang="en">
<head>
<meta charset="utf-8">
<title>KESTREL Polls – Table Slide</title>
<link rel="stylesheet" href="https://fonts.googleapis.com/css2?family=Open+Sans:wght@400;600;700&family=Roboto+Condensed:wght@400;700&family=Roboto:wght@400&display=swap">
<style>
  :root {
    --slide-blue: #0f76bc;
    --header-rule: #3cb1e9;
    --table-head: #13558b;
    --row-light: #1679c0;
    --row-dark: #1263a2;
    --grid-line: rgba(255, 255, 255, 0.28);
    --footer-grey: #9a9a9a;
    --tab-blue: #28a8e1;
    --white: #ffffff;
  }
  * { box-sizing: border-box; margin: 0; padding: 0; }
  html, body { width: 1200px; height: 900px; overflow: hidden; }
  body { background: var(--slide-blue); color: var(--white); font-family: "Roboto", Arial, sans-serif; }

  .slide { position: relative; width: 1200px; height: 900px; background: var(--slide-blue); overflow: hidden; }

  .slide-header { position: absolute; left: 0; top: 0; width: 1200px; height: 78px; }
  .slide-title {
    position: absolute; left: 19px; top: 10px;
    font-family: "Open Sans", Arial, sans-serif; font-weight: 700; font-size: 34px; letter-spacing: 0.5px;
  }
  .header-rule { position: absolute; left: 0; top: 64px; width: 1200px; height: 4px; background: var(--white); }
  .header-rule-accent { position: absolute; left: 0; top: 68px; width: 1200px; height: 5px; background: var(--header-rule); }

  .brand-tab {
    position: absolute; right: 0; top: 0; width: 176px; height: 86px;
    background: var(--white); border-bottom-left-radius: 14px;
    display: flex; align-items: center; justify-content: center; gap: 8px;
  }
  .brand-dot { width: 14px; height: 14px; border-radius: 50%; background: var(--slide-blue); }
  .brand-name { font-family: "Open Sans", Arial, sans-serif; font-weight: 700; font-size: 19px; color: var(--slide-blue); }

  .section-heading {
    position: absolute; left: 21px; top: 166px;
    font-family: "Roboto Condensed", Arial, sans-serif; font-weight: 700; font-size: 33px;
  }
  .section-intro {
    position: absolute; left: 22px; top: 216px; width: 1100px;
    font-size: 22px; line-height: 33px;
  }

  .data-table {
    position: absolute; left: 16px; top: 319px; width: 1162px;
    border-collapse: collapse; font-family: "Roboto", Arial, sans-serif;
  }
  .data-table th, .data-table td { border: 1px solid var(--grid-line); text-align: left; }
  .data-table th {
    background: var(--table-head); height: 76px; padding-left: 18px;
    font-family: "Roboto Condensed", Arial, sans-serif; font-weight: 700; font-size: 18px;
  }
  .data-table td {
    height: 57px; padding-left: 14px;
    font-family: "Roboto Condensed", Arial, sans-serif; font-size: 17px;
  }
  .data-table tbody tr:nth-child(odd) td { background: var(--row-light); }
  .data-table tbody tr:nth-child(even) td { background: var(--row-dark); }
  .data-table .col-no { width: 53px; padding-left: 0; text-align: center; }
  .data-table th.col-no { padding-left: 0; }
  .data-table .col-name { width: 249px; }
  .data-table .col-items { width: 290px; padding-left: 33px; }
  .data-table .col-code-a { width: 280px; padding-left: 34px; }
  .data-table .col-code-b { padding-left: 40px; }

  .slide-footer { position: absolute; left: 0; top: 849px; width: 1200px; height: 51px; }
  .footer-rule { position: absolute; left: 0; top: 0; width: 1200px; height: 4px; background: var(--white); }
  .footer-band { position: absolute; left: 0; top: 4px; width: 1200px; height: 47px; background: var(--footer-grey); }
  .copyright {
    position: absolute; left: 11px; top: 13px;
    font-family: "Open Sans", Arial, sans-serif; font-weight: 600; font-size: 20px;
  }
  .page-tab { position: absolute; right: 0; top: 6px; width: 112px; height: 45px; }
  .page-number {
    position: absolute; right: 24px; top: 17px;
    font-family: "Open Sans", Arial, sans-serif; font-weight: 600; font-size: 15px;
  }
</style>
</head>
<body>
<div class="slide">
  <header class="slide-header">
    <div class="header-rule"></div>
    <div class="header-rule-accent"></div>
    <h1 class="slide-title">PROJECT TITLE HERE</h1>
    <div class="brand-tab">
      <span class="brand-dot"></span>
      <span class="brand-name">KESTREL Polls</span>
    </div>
  </header>

  <h2 class="section-heading">QUISQUE RISUS MAGNA</h2>
  <p class="section-intro">Lorem ipsum dolor sit amet, consectetur adipiscing elit. Duis ut tortor vitae lorem venenatis rutrum.<br>Lorem ipsum dolor sit amet, consectetur adipiscing elit. Duis ut</p>

  <table class="data-table">
    <thead>
      <tr>
        <th class="col-no">No</th>
        <th class="col-name">Customer Name</th>
        <th class="col-items">Items</th>
        <th class="col-code-a">Subject Code</th>
        <th class="col-code-b">Subject Code</th>
      </tr>
    </thead>
    <tbody>
      <tr><td class="col-no">1</td><td class="col-name">Richard Fernendo</td><td class="col-items">Mauris laoreet commodo</td><td class="col-code-a">Mauris laoreet commodo</td><td class="col-code-b">Mauris laoreet commodo</td></tr>
      <tr><td class="col-no">2</td><td class="col-name">Richard Fernendo</td><td class="col-items">Mauris laoreet commodo</td><td class="col-code-a">Mauris laoreet commodo</td><td class="col-code-b">Mauris laoreet commodo</td></tr>
      <tr><td class="col-no">3</td><td class="col-name">Richard Fernendo</td><td class="col-items">Mauris laoreet commodo</td><td class="col-code-a">Mauris laoreet commodo</td><td class="col-code-b">Mauris laoreet commodo</td></tr>
      <tr><td class="col-no">4</td><td class="col-name">Richard Fernendo</td><td class="col-items">Mauris laoreet commodo</td><td class="col-code-a">Mauris laoreet commodo</td><td class="col-code-b">Mauris laoreet commodo</td></tr>
      <tr><td class="col-no">5</td><td class="col-name">Richard Fernendo</td><td class="col-items">Mauris laoreet commodo</td><td class="col-code-a">Mauris laoreet commodo</td><td class="col-code-b">Mauris laoreet commodo</td></tr>
      <tr><td class="col-no">6</td><td class="col-name">Richard Fernendo</td><td class="col-items">Mauris laoreet commodo</td><td class="col-code-a">Mauris laoreet commodo</td><td class="col-code-b">Mauris laoreet commodo</td></tr>
      <tr><td class="col-no">7</td><td class="col-name">Richard Fernendo</td><td class="col-items">Mauris laoreet commodo</td><td class="col-code-a">Mauris laoreet commodo</td><td class="col-code-b">Mauris laoreet commodo</td></tr>
    </tbody>
  </table>

  <footer class="slide-footer">
    <div class="footer-rule"></div>
    <div class="footer-band"></div>
    <p class="copyright">Copyright text here</p>
    <svg class="page-tab" viewBox="0 0 112 45" aria-hidden="true">
      <path d="M0 0 H112 V45 H12 L8 12 Q7 0 0 0 Z" fill="var(--tab-blue)"/>
    </svg>
    <span class="page-number">01</span>
  </footer>
</div>
</body>
</html>
```